Professional Services - letterhead / business cards

The company (velmora partners) will provide services to Investment Funds and large investors in Spain. I have recently chosen a logo that I am attaching.

I would like a simple stationary design that i could use as letter head, business cards and "with compliments" cards.

I am not quite sure which color I will mostly use for the logo, in the email signature I will probably lean towards the white background and grey letters. I am attaching my favourite options.

Target Market(s)

Large Multinationals, Investment funds and Law firms

Industry/Entity Type

Business

Requirements
Must have
• my details are:
Luis R. Abadal
Velmora Partners S.L.
Casa de Torrelumbre
Calle de Vientoalto 27
28014 Madrid
T: +34 (91) 387-2265
M: +34 (646) 819-054
e-mail: labadal@velmorapartners.com

```html
<!DOCTYPE html>
<html lang="en">
<head>
<meta charset="UTF-8">
<title>Velmora Partners – Business Card</title>
<link rel="stylesheet" href="https://fonts.googleapis.com/css2?family=Jost:wght@300;400;600&display=swap">
<style>
  :root {
    --navy: #29286a;
    --white: #ffffff;
    --grey: #7a7a7a;
    --backdrop: #e9e7e3;
    --card-w: 540px;
    --card-h: 320px;
  }
  * { box-sizing: border-box; margin: 0; padding: 0; }
  html, body { width: 1200px; height: 720px; overflow: hidden; }
  body {
    background: var(--backdrop);
    font-family: "Jost", "Century Gothic", sans-serif;
    position: relative;
  }
  .card {
    position: absolute;
    width: var(--card-w);
    height: var(--card-h);
    border-radius: 22px;
    overflow: hidden;
    box-shadow: 0 6px 18px rgba(0,0,0,0.18);
  }

  /* Front */
  .card--front { left: 40px; top: 130px; background: var(--white); }
  .front__logo {
    position: absolute; left: 0; right: 0; top: 0; height: 148px;
    display: flex; align-items: center; justify-content: center;
  }
  .wordmark {
    font-weight: 300;
    color: var(--navy);
    font-size: 46px;
    letter-spacing: 0.5px;
    white-space: nowrap;
  }
  .front__band {
    position: absolute; left: 0; right: 0; top: 148px; height: 112px;
    background: var(--navy);
    display: flex; align-items: center; justify-content: center;
    gap: 20px;
    color: var(--white);
  }
  .identity { text-align: right; }
  .identity__name {
    font-weight: 600; font-size: 22px; letter-spacing: 1.5px;
    text-transform: uppercase; line-height: 1.1;
  }
  .identity__company { font-weight: 400; font-size: 13px; line-height: 1.3; }
  .band__divider { width: 1.5px; height: 72px; background: var(--white); }
  .contact { list-style: none; font-size: 13.5px; line-height: 1.75; }
  .contact li { display: flex; align-items: center; gap: 9px; }
  .contact svg { width: 12px; height: 12px; fill: var(--white); flex: none; }
  .front__address {
    position: absolute; left: 0; right: 0; top: 260px; bottom: 0;
    display: flex; align-items: center; justify-content: center;
    color: var(--grey); font-size: 14px; letter-spacing: 0.3px;
  }

  /* Back */
  .card--back { left: 620px; top: 250px; background: var(--navy); }
  .back__logo {
    position: absolute; left: 0; right: 0; top: 70px; height: 110px;
    display: flex; align-items: center; justify-content: center;
  }
  .card--back .wordmark { color: var(--white); }
  .back__url {
    position: absolute; left: 0; right: 0; bottom: 58px;
    text-align: center; color: var(--white);
    font-size: 15px; font-weight: 600; letter-spacing: 7px;
  }
</style>
</head>
<body>

<section class="card card--front" aria-label="Business card front">
  <div class="front__logo"><span class="wordmark">velmora partners</span></div>
  <div class="front__band">
    <div class="identity">
      <p class="identity__name">Luis R. Abadal</p>
      <p class="identity__company">Velmora Partners S.L.</p>
    </div>
    <span class="band__divider"></span>
    <ul class="contact">
      <li>
        <svg viewBox="0 0 24 24" aria-hidden="true"><path d="M6.6 10.8a15.1 15.1 0 0 0 6.6 6.6l2.2-2.2c.3-.3.7-.4 1-.2 1.1.4 2.3.6 3.6.6.6 0 1 .4 1 1V20c0 .6-.4 1-1 1A17 17 0 0 1 3 4c0-.6.4-1 1-1h3.5c.6 0 1 .4 1 1 0 1.3.2 2.5.6 3.6.1.3 0 .7-.2 1z"/></svg>
        <span>+34 (91) 387-2265</span>
      </li>
      <li>
        <svg viewBox="0 0 24 24" aria-hidden="true"><path d="M7 1h10a2 2 0 0 1 2 2v18a2 2 0 0 1-2 2H7a2 2 0 0 1-2-2V3a2 2 0 0 1 2-2zm0 4v12h10V5zm5 14a1.2 1.2 0 1 0 0 2.4A1.2 1.2 0 0 0 12 19z"/></svg>
        <span>+34 (646) 819-054</span>
      </li>
      <li>
        <svg viewBox="0 0 24 24" aria-hidden="true"><path d="M2 5h20v14H2zm2 2v.5l8 5 8-5V7zm0 3v7h16v-7l-8 5z"/></svg>
        <span>labadal@velmorapartners.com</span>
      </li>
    </ul>
  </div>
  <p class="front__address">Casa de Torrelumbre, Calle de Vientoalto 27, 28014 Madrid</p>
</section>

<section class="card card--back" aria-label="Business card back">
  <div class="back__logo"><span class="wordmark">velmora partners</span></div>
  <p class="back__url">www.velmora.com</p>
</section>

</body>
</html>
```